Determining number of boxes of planks of flooring for a room

Need a creative design of an infographic of a room with instructions on how to measure the room and use this measurement to determine how much flooring to order.
The floor planks come in boxes and each box has 36 planks. Each box covers 5 metre squared in total.
The intent of the infographic is to help inform the customer how many boxes they need to order for their room.
The infographic should match the style of flooring being sold (image provided) and the logo for the company (image provided).
A crude sketch of instructions to measure a room and determine the number of boxes is provided in a document attached with this brief. Need improvement to the steps mentioned in this document on the infographic created.

```html
<!DOCTYPE html>
<html lang="en">
<head>
<meta charset="utf-8">
<title>How many boxes of planks do you need?</title>
<link href="https://fonts.googleapis.com/css2?family=Montserrat:ital,wght@0,400;0,500;0,700;0,800;1,400&display=swap" rel="stylesheet">
<style>
  :root {
    --page: #ffffff;
    --card: #5c5246;
    --room: #a7a29a;
    --room-label: #cfcac3;
    --ink: #ffffff;
    --ink-soft: #cbc3b8;
    --dark: #111111;
    --wood-warm-1: #e7b177;
    --wood-warm-2: #c98a4a;
    --wood-grey-1: #9a968f;
    --wood-grey-2: #6f6b66;
  }
  * { margin: 0; padding: 0; box-sizing: border-box; }
  html, body { width: 1200px; height: 1200px; overflow: hidden; background: var(--page); }
  body { position: relative; font-family: "Montserrat", sans-serif; color: var(--ink); }

  .infographic { position: absolute; left: 308px; top: 228px; width: 579px; height: 543px;
    background: var(--card); border-radius: 17px; }

  .hero { position: absolute; left: 319px; top: 239px; width: 557px; height: 187px; display: flex; }
  .hero-half { flex: 1; }
  .hero-warm { background: linear-gradient(160deg, var(--wood-warm-1), var(--wood-warm-2)); }
  .hero-grey { background: linear-gradient(160deg, var(--wood-grey-1), var(--wood-grey-2)); }

  .headline { position: absolute; left: 308px; width: 579px; top: 358px; text-align: center;
    font-weight: 800; font-size: 26px; line-height: 32.5px; letter-spacing: 0.6px; }
  .headline .on-photo { -webkit-text-stroke: 1px #3b3129; paint-order: stroke fill; }

  .step-number { position: absolute; width: 30px; height: 30px; border-radius: 50%;
    background: var(--ink); color: var(--card); font-weight: 800; font-size: 22px;
    display: flex; align-items: center; justify-content: center; }

  .step-text { position: absolute; font-size: 12.6px; line-height: 15.3px; font-weight: 400; }
  .step-text b { font-weight: 800; }
  .step-note { position: absolute; font-size: 9.6px; line-height: 11.6px; font-style: italic; color: var(--ink-soft); }
  .underlined { text-decoration: underline; text-underline-offset: 2px; }

  .room-plan { position: absolute; left: 505px; top: 496px; width: 186px; height: 124px; background: var(--room); }
  .room-label { position: absolute; top: 43px; font-weight: 800; font-size: 20px; color: var(--room-label); }
  .dimension { position: absolute; font-weight: 700; font-size: 12px; color: var(--dark); }

  .connectors { position: absolute; left: 0; top: 0; }

  .brand { position: absolute; left: 700px; top: 722px; display: flex; align-items: center; gap: 8px; }
  .brand-mark { width: 20px; height: 20px; background: var(--ink); }
  .brand-name { font-weight: 500; font-size: 24px; letter-spacing: 0.5px; color: var(--ink); }
</style>
</head>
<body>
  <div class="infographic"></div>

  <div class="hero" role="img" aria-label="Photos of two rooms with warm oak and grey wood-look plank flooring">
    <div class="hero-half hero-warm"></div>
    <div class="hero-half hero-grey"></div>
  </div>

  <h1 class="headline">
    <span class="on-photo">3 easy steps to determine</span><br>
    <span class="on-photo">number of boxes of planks required</span><br>
    for flooring of your room?
  </h1>

  <svg class="connectors" width="1200" height="1200" viewBox="0 0 1200 1200" aria-hidden="true">
    <g fill="none" stroke="#d8d1c6" stroke-width="0.8" stroke-dasharray="3 2">
      <polyline points="340,502 327.5,502 327.5,658 392,658"/>
      <polyline points="442,658 703.5,658 703.5,520 712,520"/>
    </g>
    <g fill="#ffffff">
      <path d="M392,655.5 L396,658 L392,660.5 Z"/>
      <path d="M712,517.5 L716,520 L712,522.5 Z"/>
    </g>
  </svg>

  <div class="step-number" style="left:348px; top:485px;">1</div>
  <p class="step-text" style="left:348px; top:516px; width:160px;">
    Measure the length (a) and width (b) of your room, in meters.
  </p>
  <p class="step-note" style="left:349px; top:569px; width:140px;">
    If your room is not a square or a rectangular shape, just sent us a simple drawing. We'll measure the room for you.
  </p>

  <div class="room-plan">
    <span class="room-label" style="left:20px;">YOUR</span>
    <span class="room-label" style="left:102px;">ROOM</span>
    <span class="dimension" style="left:78px; top:17px;">a</span>
    <span class="dimension" style="left:153px; top:85px;">b</span>
    <svg width="186" height="124" viewBox="0 0 186 124" style="position:absolute; left:0; top:0;" aria-hidden="true">
      <g stroke="#111" stroke-width="1.2" stroke-dasharray="3 2.5" fill="none">
        <line x1="93" y1="8" x2="93" y2="116"/>
        <line x1="8" y1="82" x2="178" y2="82"/>
      </g>
      <g fill="#111">
        <path d="M89,9 L93,2 L97,9 Z"/>
        <path d="M89,115 L93,122 L97,115 Z"/>
        <path d="M9,78 L2,82 L9,86 Z"/>
        <path d="M177,78 L184,82 L177,86 Z"/>
      </g>
    </svg>
  </div>

  <div class="step-number" style="left:724px; top:505px;">3</div>
  <p class="step-text" style="left:724px; top:539px; width:150px;">
    Divide room size by 5.<br>
    c ÷ 5 = <b>d</b><br>
    <span class="underlined"><b>d</b> is the number of boxes required to cover the floor.</span>
  </p>
  <p class="step-note" style="left:724px; top:622px; width:152px;">
    If d has decimal points, please round up to the next integer, e.g., if d=3.1 then round up d to 4, or if d=3.8 still round up d to 4.
  </p>

  <div class="step-number" style="left:402px; top:641px;">2</div>
  <p class="step-text" style="left:402px; top:674px; width:240px;">
    Multiply room length with room width to determine your room size.<br>
    a x b = <b>c</b><br>
    Here <b>c</b> is your room size.
  </p>

  <div class="brand">
    <span class="brand-mark"></span>
    <span class="brand-name">VELDORA</span>
  </div>
</body>
</html>
```